A restaurant needs a new design for menu and presentation flyers.

The name of the restaurant located in Germany is ,, GASTSTÄTTE AM BACH" . It means RESTAURANT THE BROOK. I attached two photos for reference to see the actual fonts.
I would like to have something close to the fonts we have now. I would like to add a crown representation.Any idea is welcomed.

Target Market(s)

GERMANY

Contact Information for Business Card

Must have AM BACH logo.

Requirements
Nice to have
• A crown representation or other symbol who can be representative for our business.
An font close to actual fonts.

```html
<!DOCTYPE html>
<html lang="en">
<head>
<meta charset="utf-8">
<title>Gaststätte Am Bach – Menu</title>
<link rel="stylesheet" href="https://fonts.googleapis.com/css2?family=Cinzel:wght@400&family=Montserrat:ital,wght@0,500;0,600;1,400&display=swap">
<style>
  :root {
    --backdrop: #55575a;
    --cover: #2c2d2f;
    --paper: #d8d2cc;
    --ink: #3a3a3a;
    --ink-soft: #7a7673;
    --band: #2f3030;
    --band-text: #e6e1dc;
    --cover-text: #d9d9d9;
    --cover-soft: #9a9a9a;
  }
  * { box-sizing: border-box; margin: 0; padding: 0; }
  html, body { width: 1200px; height: 813px; overflow: hidden; }
  body { background: var(--backdrop); position: relative; font-family: "Montserrat", sans-serif; }

  /* Cover */
  .menu-cover {
    position: absolute; left: 150px; top: 93px; width: 424px; height: 627px;
    background: var(--cover); color: var(--cover-text); text-align: center;
  }
  .brand { font-family: "Cinzel", serif; font-weight: 400; letter-spacing: 3px; }
  .menu-cover .brand { position: absolute; top: 150px; width: 100%; font-size: 34px; color: var(--cover-text); }
  .menu-title { font-family: "Cinzel", serif; letter-spacing: 12px; display: flex; justify-content: center; align-items: center; gap: 22px; }
  .menu-title .dot { width: 4px; height: 4px; background: currentColor; transform: rotate(45deg); }
  .menu-cover .menu-title { position: absolute; top: 300px; width: 100%; font-size: 32px; }
  .cover-note { position: absolute; top: 473px; width: 100%; font-size: 6px; font-style: italic; line-height: 1.45; color: var(--cover-soft); }
  .cover-web { position: absolute; top: 520px; width: 100%; font-size: 7.5px; font-weight: 600; letter-spacing: 2px; }
  .cover-social { position: absolute; top: 549px; width: 100%; display: flex; justify-content: center; gap: 28px; font-size: 5.5px; letter-spacing: 1px; color: var(--cover-soft); }

  /* Inside page */
  .menu-page { position: absolute; left: 626px; top: 136px; width: 407px; height: 541px; background: var(--paper); color: var(--ink); }
  .menu-page .brand { position: absolute; top: 52px; width: 100%; text-align: center; font-size: 30px; }
  .menu-page .menu-title { position: absolute; top: 140px; width: 100%; font-size: 24px; }
  .courses { position: absolute; top: 196px; left: 0; width: 100%; height: 200px; }
  .courses .divider { position: absolute; left: 203px; top: 12px; width: 1px; height: 176px; background: var(--ink); }
  .course-label { position: absolute; top: 0; height: 12px; background: var(--ink); color: var(--paper); font-size: 6.5px; font-weight: 600; text-align: center; line-height: 12px; letter-spacing: .5px; }
  .course-label.main { left: 22px; width: 95px; }
  .course-label.side { left: 225px; width: 95px; }
  .dish { position: absolute; width: 185px; height: 40px; }
  .dish-name { font-size: 7px; font-weight: 600; letter-spacing: .3px; }
  .dish-desc { font-size: 6px; font-style: italic; color: var(--ink-soft); line-height: 1.35; border-bottom: 1px dotted var(--ink-soft); padding-bottom: 1px; }
  .main-col .dish { left: 0; text-align: right; padding-right: 18px; }
  .main-col .dish::after { content: ""; position: absolute; right: 7px; top: 12px; width: 3px; height: 3px; border-radius: 50%; background: var(--ink); }
  .side-col .dish { left: 212px; padding-right: 40px; }
  .price { position: absolute; right: 6px; bottom: 0; font-size: 10px; font-weight: 600; }

  .drinks { position: absolute; left: 0; top: 405px; width: 100%; height: 136px; background: var(--band); color: var(--band-text); }
  .drinks-label { position: absolute; left: 130px; top: 20px; width: 148px; height: 12px; background: var(--paper); color: var(--ink); font-size: 6.5px; font-weight: 600; text-align: center; line-height: 12px; }
  .drinks .divider { position: absolute; left: 203px; top: 44px; width: 0; height: 60px; border-left: 1px dotted var(--band-text); }
  .drink { position: absolute; width: 185px; height: 30px; }
  .drink .dish-desc { color: #a9a5a1; border-bottom-color: #a9a5a1; }
  .drinks-left .drink { left: 0; text-align: right; padding: 0 18px 0 45px; }
  .drinks-left .drink::after { content: ""; position: absolute; right: 7px; top: 10px; width: 3px; height: 3px; border-radius: 50%; background: var(--band-text); }
  .drinks-left .price { left: 30px; right: auto; }
  .drinks-right .drink { left: 212px; padding-right: 40px; }
  .page-end { position: absolute; bottom: 16px; width: 100%; text-align: center; font-size: 8px; letter-spacing: 3px; }
</style>
</head>
<body>

<section class="menu-cover">
  <div class="brand">AM BACH</div>
  <h1 class="menu-title"><span class="dot"></span>MENU<span class="dot"></span></h1>
  <p class="cover-note">Ut enim ad minim veniam, quis nostrud exercitation ullamco.<br>Excepteur sint occaecat cupidatat non proident.</p>
  <p class="cover-web">WWW.AMBACH-GASTSTAETTE.DE</p>
  <ul class="cover-social" style="list-style:none">
    <li>YOUR SOCIAL PAGE</li>
    <li>YOUR PHOTO FEED</li>
    <li>YOUR MESSENGER</li>
  </ul>
</section>

<section class="menu-page">
  <div class="brand">AM BACH</div>
  <h2 class="menu-title"><span class="dot"></span>MENU<span class="dot"></span></h2>

  <div class="courses">
    <div class="course-label main">MAIN DISHES</div>
    <div class="course-label side">SIDE DISHES</div>
    <div class="divider"></div>

    <div class="main-col">
      <div class="dish" style="top:30px"><p class="dish-name">SINT OCCAECAT</p><p class="dish-desc">Ut enim ad minim veniam.</p></div>
      <div class="dish" style="top:62px"><p class="dish-name">QUIS NOSTRUD</p><p class="dish-desc">Excepteur sint occaecat cupidatat<br>non proident.</p></div>
      <div class="dish" style="top:103px"><p class="dish-name">EUISMOD TEMPOR</p><p class="dish-desc">Ut enim ad minim veniam, quis nostrud<br>exerc. ullamco.</p></div>
      <div class="dish" style="top:144px"><p class="dish-name">LOREM IPSUM</p><p class="dish-desc">Excepteur sint occaecat cupidatat<br>non proident.</p></div>
    </div>

    <div class="side-col">
      <div class="dish" style="top:30px"><p class="dish-name">SINT OCCAECAT</p><p class="dish-desc">Ut enim ad minim veniam.</p><span class="price">$5</span></div>
      <div class="dish" style="top:62px"><p class="dish-name">QUIS NOSTRUD</p><p class="dish-desc">Excepteur sint occaecat cupidatat<br>non proident.</p><span class="price">$7</span></div>
      <div class="dish" style="top:103px"><p class="dish-name">EUISMOD TEMPOR</p><p class="dish-desc">Ut enim ad minim veniam, quis<br>exerc. ullamco.</p><span class="price">$9</span></div>
      <div class="dish" style="top:144px"><p class="dish-name">LOREM IPSUM</p><p class="dish-desc">Excepteur sint occaecat cupidatat<br>non proident.</p><span class="price">$7</span></div>
    </div>
  </div>

  <div class="drinks">
    <div class="drinks-label">DRINKS</div>
    <div class="divider"></div>
    <div class="drinks-left">
      <div class="drink" style="top:50px"><p class="dish-name">SINT OCCAECAT</p><p class="dish-desc">Ut enim ad minim veniam.</p><span class="price">$5</span></div>
      <div class="drink" style="top:80px"><p class="dish-name">QUIS NOSTRUD</p><p class="dish-desc">Excepteur sint occaecat cupidatat<br>non proident.</p><span class="price">$7</span></div>
    </div>
    <div class="drinks-right">
      <div class="drink" style="top:50px"><p class="dish-name">SINT OCCAECAT</p><p class="dish-desc">Ut enim ad minim veniam.</p><span class="price">$5</span></div>
      <div class="drink" style="top:80px"><p class="dish-name">QUIS NOSTRUD</p><p class="dish-desc">Excepteur sint occaecat cupidatat<br>non proident.</p><span class="price">$7</span></div>
    </div>
    <div class="page-end">• • •</div>
  </div>
</section>

</body>
</html>
```